Meridale Bed Company Needs Business Card

Looking for a very nice looking business card. Creative but not extravagant. We sell beds and pillows across the U.S. and need something professional but catchy. I have attached the logo.

Name : Devin Holt
Title : President
Phone : (800) 471-2960
Email: sleep@quilmora.com
Website: www.quilmora.com

Can be single-sided or double-sided
horizontal or vertical

Can use Blues/Greys

Target Market(s)

Mass Market

Industry/Entity Type

Retail

Contact Information for Business Card

Name : Devin Holt
Title : President
Phone : (800) 471-2960
Email: sleep@quilmora.com
Website: www.quilmora.com

Requirements
Must have
• Clean, Modern, Smooth
• Can use Blues/Greys
• On the other side without the information - have something simple like www.quilmora.com or our logo
Nice to have
• Surprise me
Should not have
• Nothing crazy, nothing cluttered

```html
<!DOCTYPE html>
<html lang="en">
<head>
<meta charset="utf-8">
<title>Meridale Bed Company – Business Card</title>
<link rel="stylesheet" href="https://fonts.googleapis.com/css2?family=Open+Sans:wght@300;400;600;700&display=swap">
<style>
  :root {
    --page-bg: #f3f3f4;
    --card-grey: #616065;
    --brand-blue: #2bb5e8;
    --text-white: #ffffff;
    --divider: rgba(255,255,255,0.75);
  }
  * { box-sizing: border-box; margin: 0; padding: 0; }
  html, body {
    width: 1200px; height: 1200px; overflow: hidden;
    background: var(--page-bg);
    font-family: "Open Sans", Arial, sans-serif;
  }
  .sheet {
    width: 1200px; height: 1200px;
    display: flex; flex-direction: column;
    align-items: center; justify-content: center;
    gap: 56px;
  }
  .card {
    position: relative;
    width: 900px; height: 514px;
    background: var(--card-grey);
    border-radius: 16px;
    box-shadow: 0 6px 18px rgba(0,0,0,0.18);
    color: var(--text-white);
  }
  .wordmark {
    font-weight: 300;
    color: var(--brand-blue);
    letter-spacing: 4px;
    line-height: 1;
  }
  /* Front side */
  .card-front .wordmark {
    position: absolute; left: 0; right: 0; top: 170px;
    text-align: center; font-size: 128px;
  }
  .card-front .web-address {
    position: absolute; left: 0; right: 0; bottom: 96px;
    text-align: center; font-size: 20px; font-weight: 700;
    letter-spacing: 9px;
  }
  .web-address .accent { color: var(--brand-blue); }
  /* Back side */
  .card-back .wordmark {
    position: absolute; left: 0; right: 0; top: 120px;
    text-align: center; font-size: 120px;
    padding-left: 120px;
  }
  .details {
    position: absolute; left: 0; right: 0; top: 300px;
    display: flex; justify-content: center; align-items: center;
  }
  .person {
    text-align: right; padding-right: 28px;
    font-weight: 700; line-height: 1.05;
  }
  .person-name { font-size: 30px; color: var(--text-white); letter-spacing: -0.5px; }
  .person-title { font-size: 32px; color: var(--brand-blue); }
  .divider { width: 2px; height: 118px; background: var(--divider); }
  .contacts { list-style: none; padding-left: 28px; }
  .contacts li {
    display: flex; align-items: center; gap: 14px;
    font-size: 24px; font-weight: 400; line-height: 1.55;
  }
  .contacts svg { width: 22px; height: 22px; fill: var(--brand-blue); flex: none; }
</style>
</head>
<body>
<main class="sheet">
  <section class="card card-front" aria-label="Card front">
    <div class="wordmark">quilmora</div>
    <div class="web-address">www.<span class="accent">quilmora</span>.com</div>
  </section>

  <section class="card card-back" aria-label="Card back">
    <div class="wordmark">quilmora</div>
    <div class="details">
      <div class="person">
        <div class="person-name">DEVIN HOLT</div>
        <div class="person-title">President</div>
      </div>
      <div class="divider"></div>
      <ul class="contacts">
        <li>
          <svg viewBox="0 0 24 24" aria-hidden="true"><path d="M3 8c0-2 4-4 9-4s9 2 9 4v2h-5V8H8v2H3z"/><rect x="5" y="11" width="14" height="9" rx="2"/></svg>
          (800) 471-2960
        </li>
        <li>
          <svg viewBox="0 0 24 24" aria-hidden="true"><path d="M2 9l10-5 10 5v11H2z"/><path d="M2 9l10 6 10-6" fill="none" stroke="#616065" stroke-width="1.6"/></svg>
          sleep@quilmora.com
        </li>
        <li>
          <svg viewBox="0 0 24 24" aria-hidden="true"><g fill="none" stroke="#2bb5e8" stroke-width="1.8"><circle cx="12" cy="12" r="9"/><ellipse cx="12" cy="12" rx="4" ry="9"/><path d="M3 12h18M5 7h14M5 17h14"/></g></svg>
          www.quilmora.com
        </li>
      </ul>
    </div>
  </section>
</main>
</body>
</html>
```